Accountability Project Graphics

I want to create 10 social media graphics (new Instagram size 4:5 (1080 x 1350 pixels) focusing on our Quilvo Accountability App, using any of the 3 pictures attached. Use the attached pics only, NO RANDOM STOCK PHOTOGRAPHY. For the color scheme, use the landing page colors/fonts (attached).
You can add any of the 3 photos attached but I mainly need BOLD text that includes these headlines and sub-headlines on them.
Please NOTE for all the headlines below, also add this sub-headline on each graphic:
Stay Consistent with RT in Your Pocket!
Here are the headlines:
• Stop Starting Over Every Monday
• You don't need more willpower. You need more support
• Built for women who are tired of doing this alone
• When Motivation Fades, RT Checks In
• The Support System You've Been Missing
• Support When Motivation Disappears
• What if RT Checked in Every Day?
• The Missing Piece Isn't Another Diet
• Eat the food you love. Stay accountable every day.
• One Bad Meal Doesn't Mean You Failed
women over 40 trying to lose weight

```html
<!DOCTYPE html>
<html lang="en">
<head>
<meta charset="utf-8">
<title>Accountability App Social Graphics</title>
<link rel="stylesheet" href="https://fonts.googleapis.com/css2?family=Merriweather:wght@900&family=Lexend:wght@500;600&display=swap">
<style>
  :root {
    --backdrop: #a9a9a9;
    --rose: #c9577c;
    --plum: #2b1a3d;
    --blush: #fbe1ee;
    --blush-deep: #f3c9dc;
    --white: #ffffff;
    --head: "Merriweather", Georgia, serif;
    --body: "Lexend", Arial, sans-serif;
  }
  * { margin: 0; padding: 0; box-sizing: border-box; }
  html, body { width: 1200px; height: 2957px; overflow: hidden; background: var(--backdrop); }
  .board { position: relative; width: 1200px; height: 2957px; }
  .post { position: absolute; width: 431px; height: 539px; overflow: hidden; }
  .post svg.shapes { position: absolute; inset: 0; width: 431px; height: 539px; }
  .col-a { left: 156px; } .col-b { left: 612px; }
  .row-1 { top: 79px; } .row-2 { top: 645px; } .row-3 { top: 1209px; } .row-4 { top: 1774px; } .row-5 { top: 2339px; }
  .headline { position: absolute; font-family: var(--head); font-weight: 900; line-height: 1.05; }
  .tagline { position: absolute; font-family: var(--body); font-weight: 600; line-height: 1.3; }
  .white { color: var(--white); } .plum { color: var(--plum); } .rose { color: var(--rose); }
  .center { text-align: center; } .right { text-align: right; }
</style>
</head>
<body>
<svg width="0" height="0" style="position:absolute">
  <defs>
    <linearGradient id="portrait-tone" x1="0" y1="0" x2="0" y2="1">
      <stop offset="0" stop-color="#d8c7c0"/><stop offset="0.5" stop-color="#4a3a48"/><stop offset="1" stop-color="#1e2030"/>
    </linearGradient>
    <linearGradient id="hug-tone" x1="0" y1="0" x2="1" y2="1">
      <stop offset="0" stop-color="#b9a9b8"/><stop offset="0.5" stop-color="#d86a96"/><stop offset="1" stop-color="#e4f0c8"/>
    </linearGradient>
    <linearGradient id="duo-tone" x1="0" y1="0" x2="1" y2="1">
      <stop offset="0" stop-color="#e9d8c2"/><stop offset="0.5" stop-color="#3d5170"/><stop offset="1" stop-color="#33415e"/>
    </linearGradient>
    <linearGradient id="fade-blush" x1="0" y1="0" x2="1" y2="1">
      <stop offset="0" stop-color="#ffffff"/><stop offset="1" stop-color="#f6c6dc"/>
    </linearGradient>
  </defs>
</svg>

<main class="board">

  <!-- 1 -->
  <section class="post col-a row-1">
    <svg class="shapes" viewBox="0 0 431 539">
      <rect width="431" height="539" fill="var(--white)"/>
      <rect width="431" height="212" fill="var(--rose)"/>
      <circle cx="400" cy="385" r="224" fill="var(--rose)"/>
      <circle cx="430" cy="370" r="208" fill="url(#fade-blush)"/>
      <path role="img" aria-label="Portrait of the coach standing, hand on hip" d="M300 109 Q340 100 360 140 L400 200 Q431 240 431 300 L431 539 L290 539 Q270 420 250 330 Q250 240 285 200 Z" fill="url(#portrait-tone)"/>
    </svg>
    <div class="headline white" style="left:26px;top:32px;font-size:50px;">Stop Starting</div>
    <div class="headline white" style="left:26px;top:88px;font-size:44px;line-height:1.05;">Over Every<br>Monday</div>
    <div class="tagline plum" style="left:26px;top:230px;font-size:23px;">Stay<br>Consistent<br>with</div>
    <div class="tagline rose" style="left:26px;top:326px;font-size:29px;line-height:1.1;">RT in Your<br>Pocket!</div>
  </section>

  <!-- 2 -->
  <section class="post col-b row-1">
    <svg class="shapes" viewBox="0 0 431 539">
      <rect width="431" height="539" fill="var(--rose)"/>
      <path d="M0 340 Q160 420 260 330 Q330 255 431 265 L431 539 L0 539 Z" fill="var(--white)"/>
      <path d="M0 300 Q150 340 200 330 Q300 280 330 260 L431 255 L431 330 Q320 360 260 410 Q150 420 0 380 Z" fill="var(--rose)"/>
      <circle role="img" aria-label="Two women embracing and laughing" cx="212" cy="440" r="154" fill="url(#hug-tone)"/>
    </svg>
    <div class="headline white center" style="left:0;width:431px;top:22px;font-size:40px;line-height:1.12;">You don't need<br>more willpower.<br>You need<br>more support</div>
    <div class="tagline white center" style="left:0;width:431px;top:213px;font-size:22px;">Stay Consistent with<br><span style="font-size:25px">RT in Your Pocket!</span></div>
  </section>

  <!-- 3 -->
  <section class="post col-a row-2">
    <svg class="shapes" viewBox="0 0 431 539">
      <rect width="431" height="539" fill="var(--rose)"/>
      <circle cx="160" cy="430" r="162" fill="var(--white)"/>
      <circle role="img" aria-label="Two women standing side by side smiling" cx="140" cy="430" r="158" fill="url(#duo-tone)"/>
    </svg>
    <div class="headline white center" style="left:0;width:431px;top:36px;font-size:45px;line-height:1.12;">Built for women<br>who are tired of<br>doing this alone</div>
    <div class="tagline white right" style="right:28px;top:200px;font-size:22px;">Stay Consistent<br>with RT in Your<br>Pocket!</div>
  </section>

  <!-- 4 -->
  <section class="post col-b row-2">
    <svg class="shapes" viewBox="0 0 431 539">
      <rect width="431" height="539" fill="var(--white)"/>
      <circle cx="405" cy="330" r="165" fill="var(--rose)"/>
      <circle cx="95" cy="385" r="200" fill="var(--plum)"/>
      <circle role="img" aria-label="Portrait of the coach smiling, hand on hip" cx="75" cy="385" r="200" fill="url(#portrait-tone)"/>
    </svg>
    <div class="headline plum" style="left:26px;top:30px;font-size:39px;">When Motivation</div>
    <div class="headline plum" style="left:26px;top:72px;font-size:57px;">Fades,</div>
    <div class="headline rose" style="left:26px;top:137px;font-size:46px;">RT Checks In</div>
    <div class="tagline white" style="left:298px;top:245px;font-size:24px;line-height:1.3;">Stay<br>Consistent<br>with <span style="font-size:28px">RT in</span><br><span style="font-size:29px">Your<br>Pocket!</span></div>
  </section>

  <!-- 5 -->
  <section class="post col-a row-3">
    <svg class="shapes" viewBox="0 0 431 539">
      <rect width="431" height="539" fill="var(--white)"/>
      <path d="M0 140 Q60 130 120 150 L350 200 Q420 260 410 350 Q400 500 220 505 L60 505 Q0 505 0 480 Z" fill="var(--rose)"/>
      <circle cx="280" cy="55" r="165" fill="var(--plum)"/>
      <circle role="img" aria-label="Two women embracing and laughing" cx="312" cy="70" r="160" fill="url(#hug-tone)"/>
    </svg>
    <div class="headline white" style="left:26px;top:166px;font-size:47px;line-height:1.22;">The<br>Support<br>System You've<br>Been Missing</div>
    <div class="tagline white" style="left:26px;top:418px;font-size:25px;line-height:1.3;">Stay Consistent with<br>RT in Your Pocket!</div>
  </section>

  <!-- 6 -->
  <section class="post col-b row-3">
    <svg class="shapes" viewBox="0 0 431 539">
      <rect width="431" height="539" fill="var(--rose)"/>
      <path d="M135 0 Q150 130 270 165 L431 160 L431 0 Z" fill="var(--plum)"/>
      <path d="M160 0 Q180 110 290 140 L431 140 L431 0 Z" fill="var(--blush)"/>
      <path d="M0 330 Q60 330 70 420 Q80 500 150 539 L0 539 Z" fill="var(--white)"/>
      <path role="img" aria-label="Portrait of the coach standing, hand on hip" d="M300 40 Q330 30 350 70 L395 130 Q431 160 431 230 L431 539 L265 539 Q268 420 255 330 Q250 230 280 160 Z" fill="url(#portrait-tone)"/>
    </svg>
    <div class="headline white" style="left:26px;top:146px;font-size:39px;line-height:1.18;">Support<br>When<br>Motivation<br>Disappears</div>
    <div class="tagline white" style="left:94px;top:352px;font-size:23px;line-height:1.38;">Stay<br>Consistent<br>with<br><span style="font-size:28px;line-height:1.1">RT in Your<br>Pocket!</span></div>
  </section>

  <!-- 7 -->
  <section class="post col-a row-4">
    <svg class="shapes" viewBox="0 0 431 539">
      <rect width="431" height="539" fill="var(--white)"/>
      <path d="M0 0 L431 0 L431 180 Q330 180 250 210 Q150 260 0 240 Z" fill="var(--rose)"/>
      <path d="M0 0 L280 0 Q310 120 250 200 Q200 260 100 265 L0 262 Z" fill="var(--white)"/>
      <path role="img" aria-label="Portrait of the coach smiling" d="M0 0 L265 0 Q290 110 240 190 Q200 250 110 262 L0 262 Z" fill="url(#portrait-tone)"/>
    </svg>
    <div class="headline plum right" style="right:30px;top:224px;font-size:47px;line-height:1.22;">What<br>if <span class="rose">RT Checked</span><br>in Every Day?</div>
    <div class="tagline plum right" style="right:30px;top:412px;font-size:26px;line-height:1.3;">Stay Consistent with<br><span class="rose">RT in Your Pocket!</span></div>
  </section>

  <!-- 8 -->
  <section class="post col-b row-4">
    <svg class="shapes" viewBox="0 0 431 539">
      <rect width="431" height="539" fill="var(--white)"/>
      <path d="M0 0 L330 0 Q320 160 210 230 Q100 300 50 390 Q20 470 130 520 L240 539 L0 539 Z" fill="var(--rose)"/>
      <path role="img" aria-label="Two women standing side by side smiling" d="M0 0 L265 0 Q290 140 230 200 Q170 260 60 265 L0 265 Z" fill="url(#duo-tone)"/>
    </svg>
    <div class="headline plum right" style="right:30px;top:178px;font-size:47px;line-height:1.22;">The<br>Missing<br>Piece <span class="rose">Isn't</span><br><span class="rose">Another Diet</span></div>
    <div class="tagline plum right" style="right:30px;top:420px;font-size:26px;line-height:1.3;">Stay Consistent with<br><span class="rose">RT in Your Pocket!</span></div>
  </section>

  <!-- 9 -->
  <section class="post col-a row-5">
    <svg class="shapes" viewBox="0 0 431 539">
      <rect width="431" height="539" fill="var(--blush)"/>
      <circle cx="120" cy="90" r="230" fill="#ffffff" opacity="0.45"/>
      <circle cx="400" cy="120" r="200" fill="var(--blush-deep)" opacity="0.6"/>
      <circle cx="110" cy="500" r="150" fill="#ffffff" opacity="0.7"/>
      <circle cx="430" cy="470" r="190" fill="var(--rose)"/>
      <path role="img" aria-label="Portrait of the coach standing" d="M330 290 Q350 275 370 300 L395 340 Q420 360 420 400 L420 539 L300 539 Q300 460 290 410 Q290 360 320 330 Z" fill="url(#portrait-tone)"/>
    </svg>
    <div class="headline plum" style="left:26px;top:26px;font-size:57px;line-height:1.03;">Eat the food<br>you love.</div>
    <div class="headline rose" style="left:26px;top:150px;font-size:57px;line-height:1.03;">Stay<br>accountable<br>every day.</div>
    <div class="tagline plum" style="left:26px;top:380px;font-size:25px;line-height:1.3;">Stay Consistent<br>with <span class="rose">RT in Your</span><br><span class="rose">Pocket!</span></div>
  </section>

  <!-- 10 -->
  <section class="post col-b row-5">
    <svg class="shapes" viewBox="0 0 431 539">
      <rect width="431" height="539" fill="var(--rose)"/>
      <circle cx="425" cy="60" r="82" fill="var(--white)"/>
      <circle cx="260" cy="580" r="70" fill="var(--blush-deep)"/>
      <circle cx="20" cy="560" r="40" fill="var(--white)"/>
      <circle cx="370" cy="312" r="118" fill="var(--white)"/>
      <circle role="img" aria-label="Two women embracing and laughing" cx="374" cy="312" r="112" fill="url(#hug-tone)"/>
    </svg>
    <div class="headline white" style="left:26px;top:40px;font-size:54px;line-height:1.05;">One<br>Bad Meal<br>Doesn't<br>Mean<br>You<br>Failed</div>
    <div class="tagline white" style="left:26px;top:410px;font-size:24px;line-height:1.3;">Stay Consistent<br>with RT in Your<br>Pocket!</div>
  </section>

</main>
</body>
</html>
```